Natural healthcare clinic needs stationery and business card design

We have had a logo developed by Pixel Harbor and are now looking at utilising it for a new business concept. The concept is a natural healthcare clinic that hosts a number of small businesses. The individual practitioners may want to utilise the host business stationery to provide a consistent message to clients.

I am looking for a stationery design - letterhead, DL brochure template and business card that uses our logo. The business name 'Bright Meadows' is all about getting rhythm back into your life so you can be fit and healthy. The stationery design should reflect this.

There are a couple of requirements for the business card, it needs to be double-sided with black and white back. There should be lines to write appointment times on. The cards may need to be custom named on the front for example Carol Fenwick, Remedial Therapist and Aromatherapist. Therefore if a template can be provided so we can customise this information using MS Publisher, it would be appreciated.

The DL brochure template needs to be A4 folded to DL. I am looking for a consistent brand message that can be utilised to produce our own clinic brochures.

The natural healthcare clinic will host the following types of businesses - remedial massage, pregnancy massage, oncology massage, aromatherapy, acupuncture - as a bit of a guide.

Target Market(s)

25-45 year old male and females who work full time.

Industry/Entity Type

Healthcare

Requirements
Must have
• Use the logo I have already.

```html
<!DOCTYPE html>
<html lang="en">
<head>
<meta charset="utf-8">
<title>Bright Meadows Stationery</title>
<link href="https://fonts.googleapis.com/css2?family=Lato:wght@400;700&family=Libre+Baskerville&display=swap" rel="stylesheet">
<style>
  :root{
    --bg:#eeeeee;
    --paper:#ffffff;
    --leaf-dark:#3d6420;
    --leaf-mid:#6f9128;
    --leaf-light:#a9bd4c;
    --brand:#6b6a3a;
    --ink:#3a3a3a;
    --muted:#8a8a8a;
    --mono-ink:#111111;
    --mono-line:#555555;
    --shadow:0 2px 6px rgba(0,0,0,.12);
  }
  *{box-sizing:border-box;margin:0;padding:0}
  html,body{width:1200px;height:859px;overflow:hidden}
  body{background:var(--bg);font-family:"Lato",sans-serif;color:var(--ink);position:relative}
  .sheet{position:absolute;background:var(--paper);box-shadow:var(--shadow);overflow:hidden}

  .wave-area{position:absolute;left:0;right:0;bottom:0;
    background:linear-gradient(to bottom,rgba(169,189,76,0) 0%,var(--leaf-light) 30%,var(--leaf-mid) 65%,var(--leaf-dark) 100%)}

  .brand{font-family:"Lato",sans-serif;font-weight:400;color:var(--brand);white-space:nowrap;display:flex;align-items:center;gap:.35em}
  .brand-dot{width:.55em;height:.55em;border-radius:50%;background:var(--leaf-mid);flex:none}

  /* Letterhead */
  .letterhead{left:280px;top:30px;width:320px;height:452px;padding:22px 26px}
  .letterhead .brand{font-size:15px}
  .letter-contact{position:absolute;right:26px;top:24px;font-size:6px;line-height:1.5;color:var(--muted);border-left:1px solid var(--muted);padding-left:6px}
  .letter-body{margin-top:18px;font-family:"Libre Baskerville",serif;font-size:6px;line-height:1.6;max-width:230px}
  .letter-body p{margin-bottom:6px}
  .letterhead .wave-area{height:100px}

  /* Presentation cover */
  .cover{left:650px;top:30px;width:380px;height:520px}
  .cover .brand{position:absolute;left:0;right:0;top:170px;justify-content:center;font-size:36px}
  .cover .wave-area{height:170px}

  /* Business cards */
  .card{width:210px;height:120px}
  .card-front{left:30px;top:270px}
  .card-front .brand{position:absolute;left:18px;top:22px;font-size:18px}
  .card-front .wave-area{height:46px}

  .card-back{left:30px;top:410px;padding:12px 14px;color:var(--mono-ink)}
  .card-back .person{font-size:9px;font-weight:700}
  .card-back .role{font-size:7px;line-height:1.4}
  .card-back .brand{position:absolute;right:14px;top:12px;font-size:9px;color:var(--mono-ink)}
  .card-back .brand-dot{background:var(--mono-ink)}
  .appointments{margin-top:6px;font-size:6.5px}
  .appointments .heading{font-weight:700;margin-bottom:2px}
  .appt-line{display:flex;gap:4px;align-items:flex-end;height:12px}
  .appt-line span{flex:none}
  .appt-line i{flex:1;border-bottom:1px solid var(--mono-line)}

  /* Compliment slip */
  .slip{left:260px;top:520px;width:360px;height:190px}
  .slip .brand{position:absolute;right:22px;top:56px;font-size:13px}
  .slip .wave-area{height:90px}

  /* Envelope */
  .envelope{left:650px;top:590px;width:480px;height:230px}
  .envelope .flap{position:absolute;left:0;top:0;width:100%;height:70px;border-bottom:1px solid #e2e2e2;background:#fafafa;display:flex;align-items:center;justify-content:center}
  .envelope .brand{font-size:15px}
</style>
</head>
<body>

<section class="sheet letterhead" aria-label="Letterhead">
  <div class="brand"><span class="brand-dot"></span>Bright Meadows</div>
  <div class="letter-contact">
    <div>Tel 555 0142</div>
    <div>Fax 555 0143</div>
    <div>hello@brightmeadows.example</div>
  </div>
  <div class="letter-body">
    <p>18 Fern Hollow Road<br>Greenvale, CA 90210</p>
    <p>January 12, 2024</p>
    <p>Ms. Dana Holt<br>Riverside Wellness Centre<br>Greenvale, CA 90211</p>
    <p>Dear Ms. Holt,</p>
    <p>Thank you for visiting our clinic last week. We are pleased to share details of our new treatment rooms and practitioners.</p>
    <p>Please find our schedule enclosed.</p>
    <p>Sincerely,<br>Carol Fenwick</p>
  </div>
  <div class="wave-area" role="img" aria-label="Flowing green wave decoration"></div>
</section>

<section class="sheet cover" aria-label="Presentation cover">
  <div class="brand"><span class="brand-dot"></span>Bright Meadows</div>
  <div class="wave-area" role="img" aria-label="Flowing green wave decoration"></div>
</section>

<section class="sheet card card-front" aria-label="Business card front">
  <div class="brand"><span class="brand-dot"></span>Bright Meadows</div>
  <div class="wave-area" role="img" aria-label="Flowing green wave decoration"></div>
</section>

<section class="sheet card card-back" aria-label="Business card back, black and white">
  <div class="person">Carol Fenwick</div>
  <div class="role">Remedial Therapist &amp; Aromatherapist</div>
  <div class="brand"><span class="brand-dot"></span>Bright Meadows</div>
  <div class="appointments">
    <div class="heading">Your next appointment</div>
    <div class="appt-line"><span>Date</span><i></i><span>Time</span><i></i></div>
    <div class="appt-line"><span>Date</span><i></i><span>Time</span><i></i></div>
    <div class="appt-line"><span>Date</span><i></i><span>Time</span><i></i></div>
    <div class="appt-line"><span>Tel 555 0142</span></div>
  </div>
</section>

<section class="sheet slip" aria-label="Compliment slip">
  <div class="brand"><span class="brand-dot"></span>Bright Meadows</div>
  <div class="wave-area" role="img" aria-label="Flowing green wave decoration"></div>
</section>

<section class="sheet envelope" aria-label="DL envelope">
  <div class="flap">
    <div class="brand"><span class="brand-dot"></span>Bright Meadows</div>
  </div>
</section>

</body>
</html>
```